Spring Detox sale graphics for social media

You MUST read the Brief in the WORD document and follow the instructions there. I want to create 10 social media graphics (new Instagram size 4:5 (1080 x 1350 pixels) focusing on our Mother’s Day Spring Detox Sale graphics, using any of the pics attached. Use the attached pics, NO RANDOM STOCK PHOTOGRAPHY. For the color scheme of the graphics, they should all be complementary to the product colors or feel like Spring time.

Target Market(s)

primarily women

Requirements
Must have
• the photos and text attached

```html
<!DOCTYPE html>
<html lang="en">
<head>
<meta charset="UTF-8">
<title>Spring Detox Sale</title>
<link href="https://fonts.googleapis.com/css2?family=Pacifico&family=Montserrat:wght@900&family=Poppins:wght@700;800&family=Varela+Round&display=swap" rel="stylesheet">
<style>
  :root {
    --sky-top: #f2f5fa;
    --sky-mid: #eef2f8;
    --sky-low: #f6f8fb;
    --script-blue: #2a5bc7;
    --detox-red: #e42c2c;
    --outline-blue: #2f5fc9;
    --pill-plum: #7a3a5c;
    --white: #ffffff;
    --badge-red: #e3262b;
    --blossom-pink: rgba(240, 186, 200, 0.95);
    --blossom-soft: rgba(246, 214, 222, 0.9);
    --blossom-leaf: rgba(190, 220, 150, 0.8);
    --grass-light: #e4f1c2;
    --grass-green: #c6e08a;
    --bottle-white: #f4f5f7;
    --label-blue: #2d46b5;
    --label-green: #2f7a5c;
    --label-pink: #c9489a;
    --label-red: #e0282c;
  }
  * { margin: 0; padding: 0; box-sizing: border-box; }
  html, body { width: 960px; height: 1200px; overflow: hidden; }
  body { background: var(--sky-top); }
  .poster {
    position: relative;
    width: 960px;
    height: 1200px;
    overflow: hidden;
    background: linear-gradient(180deg, var(--sky-top) 0%, var(--sky-mid) 45%, var(--sky-low) 100%);
  }
  .blossom-branches {
    position: absolute;
    left: 0; top: 0;
    width: 960px; height: 270px;
    background:
      radial-gradient(circle 46px at 60px 40px, var(--blossom-pink), rgba(240,186,200,0) 100%),
      radial-gradient(circle 40px at 150px 95px, var(--blossom-pink), rgba(240,186,200,0) 100%),
      radial-gradient(circle 34px at 40px 115px, var(--blossom-soft), rgba(246,214,222,0) 100%),
      radial-gradient(circle 44px at 230px 25px, var(--blossom-pink), rgba(240,186,200,0) 100%),
      radial-gradient(circle 36px at 340px 60px, var(--blossom-soft), rgba(246,214,222,0) 100%),
      radial-gradient(circle 32px at 460px 10px, var(--blossom-soft), rgba(246,214,222,0) 100%),
      radial-gradient(circle 26px at 550px 30px, var(--blossom-leaf), rgba(190,220,150,0) 100%),
      radial-gradient(circle 38px at 650px 20px, var(--blossom-pink), rgba(240,186,200,0) 100%),
      radial-gradient(circle 40px at 760px 50px, var(--blossom-pink), rgba(240,186,200,0) 100%),
      radial-gradient(circle 46px at 890px 35px, var(--blossom-pink), rgba(240,186,200,0) 100%),
      radial-gradient(circle 42px at 905px 140px, var(--blossom-pink), rgba(240,186,200,0) 100%),
      radial-gradient(circle 30px at 830px 165px, var(--blossom-soft), rgba(246,214,222,0) 100%),
      radial-gradient(circle 28px at 940px 200px, var(--blossom-leaf), rgba(190,220,150,0) 100%),
      radial-gradient(circle 24px at 110px 175px, var(--blossom-leaf), rgba(190,220,150,0) 100%);
  }
  .headline {
    position: absolute;
    left: 0; top: 222px;
    width: 960px;
    height: 200px;
    text-align: center;
    font-weight: normal;
  }
  .headline-script {
    display: block;
    margin-left: 36px;
    font-family: 'Pacifico', cursive;
    font-size: 96px;
    line-height: 1;
    color: var(--script-blue);
  }
  .headline-main {
    position: absolute;
    left: 210px; top: 106px;
    white-space: nowrap;
    line-height: 1;
  }
  .headline-detox {
    font-family: 'Montserrat', sans-serif;
    font-weight: 900;
    font-size: 94px;
    letter-spacing: -2px;
    color: var(--detox-red);
  }
  .headline-sale {
    margin-left: 16px;
    font-family: 'Varela Round', sans-serif;
    font-size: 104px;
    color: transparent;
    -webkit-text-stroke: 2px var(--outline-blue);
  }
  .offer-pill {
    position: absolute;
    left: 296px; top: 420px;
    width: 399px; height: 51px;
    border-radius: 26px;
    background: var(--pill-plum);
    color: var(--white);
    font-family: 'Poppins', sans-serif;
    font-weight: 700;
    font-size: 25px;
    line-height: 51px;
    text-align: center;
    letter-spacing: 0.3px;
  }
  .product {
    position: absolute;
    border-radius: 30px 30px 22px 22px;
    box-shadow: 0 10px 18px rgba(80, 90, 110, 0.12);
  }
  .product-blood-sugar {
    left: 116px; top: 564px; width: 191px; height: 454px; z-index: 1;
    background: linear-gradient(180deg, var(--bottle-white) 0%, #e9ecf4 60%, var(--label-blue) 86%, var(--bottle-white) 92%);
  }
  .product-hormone {
    left: 267px; top: 556px; width: 178px; height: 466px; z-index: 2;
    background: linear-gradient(180deg, var(--bottle-white) 0%, #e8efec 60%, var(--label-green) 86%, var(--bottle-white) 92%);
  }
  .product-tummy {
    left: 631px; top: 553px; width: 227px; height: 465px; z-index: 2;
    background: linear-gradient(180deg, var(--bottle-white) 0%, #f1e8e8 60%, var(--label-red) 86%, var(--bottle-white) 92%);
  }
  .product-liver {
    left: 396px; top: 562px; width: 262px; height: 469px; z-index: 3;
    background: linear-gradient(180deg, var(--bottle-white) 0%, #f1e6ec 60%, var(--label-pink) 86%, var(--bottle-white) 92%);
  }
  .discount-badge {
    position: absolute;
    left: 780px; top: 500px;
    width: 160px; height: 160px;
    z-index: 5;
  }
  .discount-badge svg { width: 160px; height: 160px; display: block; }
  .discount-badge-text {
    position: absolute;
    left: 0; top: 0;
    width: 160px; height: 160px;
    display: flex;
    flex-direction: column;
    align-items: center;
    justify-content: center;
    color: var(--white);
    font-family: 'Poppins', sans-serif;
    font-weight: 800;
    line-height: 1;
  }
  .discount-badge-value { font-size: 46px; letter-spacing: -1px; }
  .discount-badge-label { font-size: 30px; margin-top: 2px; }
  .spring-grass {
    position: absolute;
    left: 0; top: 960px;
    width: 960px; height: 240px;
    z-index: 4;
    background:
      radial-gradient(ellipse 60px 130px at 290px 240px, rgba(170,205,120,0.55), rgba(170,205,120,0) 100%),
      radial-gradient(ellipse 50px 150px at 870px 240px, rgba(170,205,120,0.55), rgba(170,205,120,0) 100%),
      linear-gradient(180deg, rgba(228,241,194,0) 0%, rgba(228,241,194,0.7) 40%, var(--grass-green) 100%);
  }
</style>
</head>
<body>
  <main class="poster">
    <div class="blossom-branches" role="img" aria-label="Pink cherry blossom branches with green leaves across the top"></div>

    <h1 class="headline">
      <span class="headline-script">Spring</span>
      <span class="headline-main"><span class="headline-detox">Detox</span><span class="headline-sale">Sale!</span></span>
    </h1>

    <div class="offer-pill">25% OFF ALL SUPPLEMENTS</div>

    <div class="product product-blood-sugar" role="img" aria-label="White supplement bottle with a blue blood sugar label"></div>
    <div class="product product-hormone" role="img" aria-label="White supplement bottle with a green hormone label"></div>
    <div class="product product-tummy" role="img" aria-label="White supplement bottle with a red digestive cleanse label"></div>
    <div class="product product-liver" role="img" aria-label="White supplement bottle with a pink liver detox label"></div>

    <div class="discount-badge">
      <svg viewBox="0 0 160 160" aria-hidden="true">
        <g fill="var(--badge-red)">
          <circle cx="80" cy="80" r="68"/>
          <circle cx="80" cy="16" r="16"/>
          <circle cx="125.3" cy="34.7" r="16"/>
          <circle cx="144" cy="80" r="16"/>
          <circle cx="125.3" cy="125.3" r="16"/>
          <circle cx="80" cy="144" r="16"/>
          <circle cx="34.7" cy="125.3" r="16"/>
          <circle cx="16" cy="80" r="16"/>
          <circle cx="34.7" cy="34.7" r="16"/>
        </g>
      </svg>
      <div class="discount-badge-text">
        <span class="discount-badge-value">25%</span>
        <span class="discount-badge-label">OFF</span>
      </div>
    </div>

    <div class="spring-grass" role="img" aria-label="Soft green spring grass along the bottom edge"></div>
  </main>
</body>
</html>
```